Web Developer Wordpress theme

I'm a web developer but a poor designer so i need somebody to design me a cool and professional WordPress theme. I specialize in shopping cart developments and modifications as well as hosting for these system so would like the design to show this off. I am UK based and want this to also come across in the design.
As for colors and layout i am open mined just use your imaginantion i will let know what i think of your designs.
also forgot to mention my business name is valtrique
and my exsiting site is valtrique.co.uk

```html
<!DOCTYPE html>
<html lang="en">
<head>
<meta charset="utf-8">
<title>Valtrique – Serious Web Development</title>
<link href="https://fonts.googleapis.com/css2?family=Questrial&family=Arimo:wght@400;700&display=swap" rel="stylesheet">
<style>
:root{
  --ink:#1b1b1b;
  --header-top:#3a3a3a;
  --header-bottom:#0c0c0c;
  --orange:#f7941d;
  --orange-dark:#e06a0a;
  --blue:#2b9be0;
  --blue-dark:#0f64a8;
  --hero-bg:#f1f1f1;
  --hero-stripe:#e6e6e6;
  --text-grey:#4a4a4a;
  --dark-bg:#161616;
  --card-bg:#111;
  --light-bg:#e9e9e9;
  --white:#fff;
}
*{box-sizing:border-box;margin:0;padding:0}
html,body{width:801px;height:1200px;overflow:hidden}
body{position:relative;background:var(--white);font-family:"Arimo",Arial,sans-serif;color:var(--ink)}
.abs{position:absolute}

/* header */
.site-header{left:0;top:0;width:801px;height:147px;background:linear-gradient(var(--header-top),var(--header-bottom))}
.brand{left:18px;top:28px;display:flex;align-items:center;gap:12px}
.brand-mark{width:62px;height:62px;border-radius:10px;background:linear-gradient(#fff,#d9d9d9)}
.brand-name{font-family:"Questrial",sans-serif;font-size:46px;color:var(--orange);line-height:1}
.brand-tag{left:96px;top:94px;font-family:"Questrial",sans-serif;font-size:9px;letter-spacing:2px;color:#aaa}
.nav-item{width:60px;height:60px;top:37px}
.nav-item .diamond{position:absolute;inset:0;transform:rotate(45deg) scale(.72);border-radius:6px;background:linear-gradient(#ffb13b,var(--orange-dark));box-shadow:0 3px 6px rgba(0,0,0,.5)}
.nav-item.active .diamond{background:linear-gradient(#54b9f2,var(--blue-dark))}
.nav-item span{position:absolute;inset:0;display:flex;align-items:center;justify-content:center;text-align:center;font-size:12px;line-height:1.15;color:var(--white)}
.nav-item:not(.active) span{color:#3a1e00}

/* hero */
.hero{left:0;top:147px;width:801px;height:313px;background:repeating-linear-gradient(90deg,var(--hero-bg) 0 14px,var(--hero-stripe) 14px 16px)}
.hero-title{left:13px;top:193px;font-family:"Questrial",sans-serif;font-size:35px;color:var(--orange-dark)}
.hero-text{left:14px;top:256px;width:263px;font-family:"Questrial",sans-serif;font-size:18px;line-height:24px;color:var(--text-grey);text-align:justify}
.read-more{left:133px;top:371px;width:140px;height:36px;border-radius:5px;background:linear-gradient(#5fc0f5,var(--blue-dark));display:flex;align-items:center;justify-content:center;font-family:"Questrial",sans-serif;font-size:20px;color:#0a2d4c}
.hero-visual{left:396px;top:169px;width:284px;height:264px;background:linear-gradient(#2a2a2a,#0b0b0b);border-radius:6px;padding:14px}
.hero-visual div{width:100%;height:190px;background:linear-gradient(135deg,#f4f4f4,#bfbfbf 60%,#86c440)}

/* projects */
.projects{left:0;top:460px;width:801px;height:360px;background:var(--dark-bg)}
.projects h2{left:22px;top:477px;font-family:"Questrial",sans-serif;font-weight:400;font-size:19px;color:var(--white)}
.projects p{left:24px;width:754px;font-size:9.3px;line-height:13px;color:#d8d8d8}
.project{width:117px;height:117px;top:624px;transform:rotate(45deg);border-radius:12px;overflow:hidden}
.project div{width:100%;height:100%}
.project-label{font-family:"Questrial",sans-serif;font-size:17px;color:var(--white);transform:rotate(-45deg);transform-origin:left bottom;white-space:nowrap}
.arrow{top:672px}

/* services */
.services{left:0;top:820px;width:801px;height:327px;background:var(--light-bg)}
.services-frame{left:24px;top:867px;width:753px;height:260px;border:4px solid var(--blue);border-radius:8px;background:#f3f3f3}
.services-tab{left:300px;top:842px;width:200px;height:29px;background:var(--blue);border-radius:30px 30px 0 0;color:var(--white);font-family:"Questrial",sans-serif;font-size:19px;display:flex;align-items:center;justify-content:center}
.card{top:900px;width:212px;height:204px;background:var(--card-bg);border-radius:4px}
.card-head{position:absolute;left:0;top:0;width:100%;height:66px;background:linear-gradient(#3b3b3b,#1a1a1a)}
.card-icon{position:absolute;left:6px;top:-10px;width:66px;height:66px;transform:rotate(45deg) scale(.82);border-radius:8px;background:var(--white);padding:6px}
.card-icon div{width:100%;height:100%;border-radius:4px}
.card h3{position:absolute;right:12px;top:18px;text-align:right;font-family:"Questrial",sans-serif;font-weight:400;font-size:18.5px;line-height:21px;color:var(--white)}
.card p{position:absolute;left:14px;top:76px;width:184px;font-size:9.5px;line-height:13.4px;color:#e0e0e0;text-align:justify;text-align-last:right}
.card .detail{position:absolute;right:0;bottom:0;width:66px;height:22px;background:linear-gradient(var(--blue),var(--blue-dark));border-radius:6px 0 4px 0;color:var(--white);font-size:11px;display:flex;align-items:center;justify-content:center}

/* footer */
.site-footer{left:0;top:1147px;width:801px;height:53px;background:linear-gradient(#fff,#ececec)}
.footer-brand{left:52px;top:1160px;display:flex;align-items:center;gap:5px;font-family:"Questrial",sans-serif;font-size:20px;color:var(--orange)}
.footer-brand i{width:14px;height:14px;background:var(--blue-dark)}
.footer-nav{left:159px;top:1162px;font-size:9.5px;color:#333}
.footer-nav .current{color:var(--blue)}
.copyright{left:159px;top:1178px;font-size:9.5px;color:#333}
.social{top:1162px;width:28px;height:28px;border-radius:50%;background:linear-gradient(#aaa,#555)}
.social.mail{background:linear-gradient(#ffae3a,var(--orange-dark))}
</style>
</head>
<body>

<header class="site-header abs"></header>
<div class="brand abs"><div class="brand-mark"></div><span class="brand-name">valtrique</span></div>
<div class="brand-tag abs">serious web development</div>
<nav>
  <a class="nav-item active abs" style="left:514px"><i class="diamond"></i><span>Home</span></a>
  <a class="nav-item abs" style="left:575px"><i class="diamond"></i><span>About<br>Us</span></a>
  <a class="nav-item abs" style="left:635px"><i class="diamond"></i><span>Work</span></a>
  <a class="nav-item abs" style="left:697px"><i class="diamond"></i><span>Contact<br>Us</span></a>
</nav>

<section class="hero abs"></section>
<h1 class="hero-title abs" style="font-weight:400">Lorem Ipsum Dolor</h1>
<p class="hero-text abs">Lorem ipsum dolor sit amet, consectetur adipiscing elit. Phasellus et sapien id neque posuere pharetra eu ac urna.</p>
<a class="read-more abs">Read More</a>
<div class="hero-visual abs" role="img" aria-label="Monitor showing a business figure standing on green and grey puzzle pieces"><div></div></div>

<section class="projects abs"></section>
<div class="projects">
  <h2 class="abs">Recent Projects</h2>
  <p class="abs" style="top:514px">Lorem ipsum dolor sit amet, consectetur adipiscing elit. Phasellus et sapien id neque posuere pharetra eu ac urna. Quisque aliquam vulputate elit, sit amet tempor quam lacinia at. Sed ullamcorper, ipsum eu dapibus commodo, elit dui pulvinar massa, a laoreet neque nisi eu erat. Proin vel metus sed sapien faucibus venenatis id ac massa.</p>
  <p class="abs" style="top:548px">Sed ullamcorper, ipsum eu dapibus commodo, elit dui pulvinar massa, a laoreet neque nisi eu erat. Proin vel metus sed sapien faucibus venenatis id ac massa.</p>
</div>
<svg class="arrow abs" style="left:14px" width="10" height="24"><path d="M9 0 L0 12 L9 24Z" fill="#555"/></svg>
<svg class="arrow abs" style="left:777px" width="10" height="24"><path d="M1 0 L10 12 L1 24Z" fill="#555"/></svg>

<div class="project abs" style="left:71px" role="img" aria-label="Magnifying glass over a keyboard with a green chart"><div style="background:linear-gradient(135deg,#7fbf3f,#e8e8e8 55%,#9a9a9a)"></div></div>
<div class="project abs" style="left:251px" role="img" aria-label="Hands holding a tablet showing a project diagram"><div style="background:linear-gradient(135deg,#3a3a3a,#d8d8d8 55%,#3aa83a)"></div></div>
<div class="project abs" style="left:431px" role="img" aria-label="Shopping cart full of colourful app icons"><div style="background:linear-gradient(135deg,#5fb63a,#e05050 45%,#4a8fd8)"></div></div>
<div class="project abs" style="left:614px" role="img" aria-label="Hand writing on paper beside a laptop"><div style="background:linear-gradient(135deg,#2a6aa0,#e4e4e4 55%,#58b030)"></div></div>

<span class="project-label abs" style="left:44px;top:640px">Lorem Ipsum</span>
<span class="project-label abs" style="left:224px;top:640px">Lorem Ipsum</span>
<span class="project-label abs" style="left:404px;top:640px">Lorem Ipsum</span>
<span class="project-label abs" style="left:587px;top:640px">Lorem Ipsum</span>

<section class="services abs"></section>
<div class="services-frame abs"></div>
<div class="services-tab abs">Services</div>

<article class="card abs" style="left:51px">
  <div class="card-head"></div>
  <div class="card-icon" role="img" aria-label="Blue site map boxes"><div style="background:linear-gradient(#7cc4f2,#1e73c0)"></div></div>
  <h3>Web<br>Developement</h3>
  <p>Lorem ipsum dolor sit amet, consectetur adipiscing elit. Lorem ipsum dolor sit amet, consectetur adipiscing elit. Phasellus et sapien id neque posuere pharetra eu ac urna. Quisque aliquam vulputate elit, sit amet tempor quam lacinia at. Sed ullamcorper, ipsum eu dapibus</p>
  <a class="detail">Detail</a>
</article>
<article class="card abs" style="left:295px">
  <div class="card-head"></div>
  <div class="card-icon" role="img" aria-label="Hand cursor clicking a green add to cart key"><div style="background:linear-gradient(#6fc25a,#2a8a2a)"></div></div>
  <h3>Shopping Cart<br>Maintenance</h3>
  <p>Lorem ipsum dolor sit amet, consectetur adipiscing elit. Lorem ipsum dolor sit amet, consectetur adipiscing elit. Phasellus et sapien id neque posuere pharetra eu ac urna. Quisque aliquam vulputate elit, sit amet tempor quam lacinia at. Sed ullamcorper, ipsum eu dapibus</p>
  <a class="detail">Detail</a>
</article>
<article class="card abs" style="left:539px">
  <div class="card-head"></div>
  <div class="card-icon" role="img" aria-label="Network of grey server icons"><div style="background:linear-gradient(#f2f2f2,#9a9a9a)"></div></div>
  <h3>Shopping Cart<br>Hosting</h3>
  <p>Lorem ipsum dolor sit amet, consectetur adipiscing elit. Lorem ipsum dolor sit amet, consectetur adipiscing elit. Phasellus et sapien id neque posuere pharetra eu ac urna. Quisque aliquam vulputate elit, sit amet tempor quam lacinia at. Sed ullamcorper, ipsum eu dapibus</p>
  <a class="detail">Detail</a>
</article>

<footer class="site-footer abs"></footer>
<div class="footer-brand abs"><i></i>valtrique</div>
<div class="footer-nav abs"><span class="current">Home</span> &nbsp;| &nbsp;About Us &nbsp;| &nbsp;Work &nbsp;| &nbsp;Privacy Policy</div>
<div class="copyright abs">CopyRights 2012 All Rights Reserved</div>
<svg class="social mail abs" style="left:650px" width="28" height="28" viewBox="0 0 28 28"><rect x="7" y="9" width="14" height="10" rx="1" fill="#fff"/><path d="M7 9 L14 15 L21 9" fill="none" stroke="#e06a0a" stroke-width="1.3"/></svg>
<div class="social abs" style="left:686px"></div>
<div class="social abs" style="left:721px"></div>

</body>
</html>
```